Zielgruppe
Wir sind ein Netzwerk aus unabhängigen Tierarztpraxen und-kliniken.
Aufgabenstellung
1. Allgemeine Anforderungen:
Wir benötigen ein Set an Masterfolien für unsere Präsentationen. Als Orientierung stellen wir Ihnen einige Beispielfolien im Anhang zur Verfügung, die eine grobe Vorstellung davon vermitteln, wie das Design aussehen soll. Zudem empfehlen wir, sich auf unserer Homepage umzusehen, um sicherzustellen, dass das Design mit unserem bestehenden Corporate Design harmoniert.
2. Farbkonzept:
Bitte verwenden Sie unsere definierten Unternehmensfarben:
Gelb: #f7cd4e
Blau: #143357
Gold: #9d8030
Weiß: #ffffff
3. Schriftarten:
Unsere Unternehmensschriftarten sind:
Raleway
Century Gothic
Bitte stellen Sie sicher, dass diese Fonts durchgehend verwendet werden.
4. Farbvarianten:
Wir wünschen uns drei unterschiedliche Farbvarianten der Masterfolien:
Blaue Version: mit Blau als dominierende Farbe
Gelbe Version: mit Gelb als dominierende Farbe
Neutrale Version: weiß dominierend mit - eine ausgewogene Mischung mit gedeckteren Farben
5. Design-Elemente:
Das Design sollte modern, professionell und klar strukturiert sein.
Die Masterfolien sollen verschiedene Layouts enthalten (Titelfolie, Inhaltsfolie, Bild-Text-Kombinationen, etc.).
Bitte achten Sie darauf, dass genügend weißer Raum für eine aufgeräumte und übersichtliche Gestaltung bleibt.
Elemente wie Linien, Icons oder dezente Muster können genutzt werden, sollten jedoch nicht zu dominant wirken.
6. Format:
Die Masterfolien sollten für Microsoft PowerPoint optimiert sein und in 16:9 Format erstellt werden.

```html
<!DOCTYPE html>
<html lang="de">
<head>
<meta charset="utf-8">
<title>KLUVOTREN Masterfolien</title>
<link href="https://fonts.googleapis.com/css2?family=Raleway:ital,wght@0,500;0,600;0,700;0,800;1,500;1,600&family=Questrial&display=swap" rel="stylesheet">
<style>
:root{
  --yellow:#f7cd4e;
  --blue:#143357;
  --gold:#9d8030;
  --white:#ffffff;
  --page:#f1f1f1;
  --photo-a:#8aa0b8;
  --photo-b:#d9dfe6;
}
*{margin:0;padding:0;box-sizing:border-box}
html,body{width:1200px;height:2654px;overflow:hidden;background:var(--page)}
.board{position:absolute;left:0;top:0;width:1165px;height:2577px;transform:scale(1.0300);transform-origin:0 0;font-family:"Questrial",sans-serif;color:var(--blue)}
.slide{position:absolute;width:507px;height:285px;overflow:hidden;background:var(--yellow)}
.slide--blue{background:var(--blue)}
.abs{position:absolute}
.slide-title{position:absolute;left:38px;top:30px;font:700 20px/1.1 "Raleway",sans-serif;color:var(--blue);white-space:nowrap}
.slide-title::before{content:"";position:absolute;left:0;top:-8px;width:22px;height:2px;background:var(--blue)}
.mark{position:absolute;right:24px;top:17px;display:flex;flex-direction:column;align-items:center;gap:2px}
.mark__dot{width:14px;height:14px;border-radius:50%;border:1.5px solid var(--gold);opacity:.8}
.mark__name{font:700 5px/1 "Raleway",sans-serif;color:var(--gold);letter-spacing:.2px;opacity:.85}
.foot{position:absolute;left:19px;bottom:13px;font-size:5.5px;color:var(--blue);white-space:nowrap}
.foot--light{color:var(--white)}
.pg{position:absolute;right:0;bottom:0;width:70px;height:27px;background:var(--blue);border-radius:10px 0 0 0;color:var(--white);font:700 19px/27px "Raleway",sans-serif;text-align:center}
.pg--yellow{background:var(--yellow)}
.txt{font-size:6.4px;line-height:1.65;color:var(--blue)}
.bold{font:700 6.6px/1.6 "Raleway",sans-serif;color:var(--blue)}
.photo{position:absolute;background:linear-gradient(150deg,var(--photo-b),var(--photo-a));border-radius:10px}
.photo--fade{opacity:.35}
.btn{position:absolute;height:22px;border-radius:8px;background:var(--yellow);display:flex;align-items:center;gap:8px;padding:0 12px;font:700 8px/1 "Raleway",sans-serif;color:var(--blue)}
.btn svg{width:9px;height:9px}
.brand{position:absolute;display:flex;align-items:center;gap:8px}
.brand__dot{width:24px;height:24px;border-radius:50%;border:2px solid var(--gold)}
.brand__name{font:700 19px/1 "Raleway",sans-serif;color:var(--gold);letter-spacing:.5px}
.cover-title{position:absolute;font:700 22px/1.35 "Raleway",sans-serif;color:var(--white)}
.cover-title em{font-style:normal;color:var(--yellow)}
.cover-foot{position:absolute;bottom:13px;font-size:5.3px;color:var(--white);white-space:nowrap}
.pattern-area{position:absolute;left:0;top:150px;width:130px;height:135px;background:linear-gradient(45deg,rgba(20,51,87,.12),rgba(20,51,87,0) 70%)}
.agenda-item{position:absolute;display:flex;gap:10px;font-size:6.2px;line-height:1.7}
.agenda-item b{font:700 7.5px/1.2 "Raleway",sans-serif}
.agenda-item strong{font:700 6.4px/1.6 "Raleway",sans-serif;display:block}
.list-row{position:absolute;left:258px;width:190px;display:flex;gap:15px;font-size:6.4px;line-height:1.65}
.list-row b{font-weight:400}
.rule{position:absolute;left:258px;width:190px;height:.7px;background:var(--blue)}
.card{position:absolute;background:var(--white);border-radius:8px}
.icon-box{position:absolute;background:var(--blue);border-radius:7px;display:flex;align-items:center;justify-content:center}
.icon-box svg{stroke:var(--white)}
.ico{fill:none;stroke-width:1.6;stroke-linecap:round;stroke-linejoin:round}
.quart{position:absolute;width:72px;height:70px;display:flex;align-items:center;justify-content:center;text-align:center;font:700 9px/1.25 "Raleway",sans-serif}
.quart--white{background:var(--white);color:var(--blue)}
.quart--blue{background:var(--blue);color:var(--white)}
.plist{position:absolute;font-size:5.8px;line-height:1.75}
.plist strong{display:block;font:700 6.4px/1.8 "Raleway",sans-serif}
.pill{position:absolute;left:270px;width:188px;height:30px;background:var(--white);border-radius:8px;padding:6px 0 0 12px;font:700 6.4px/1.55 "Raleway",sans-serif}
.pill__icon{position:absolute;right:6px;top:5px;width:20px;height:20px;border-radius:50%;border:2px solid var(--yellow);display:flex;align-items:center;justify-content:center}
.pill__icon svg{stroke:var(--blue)}
.team-card{position:absolute;top:85px;width:104px;height:165px;background:var(--white);border-radius:9px;overflow:hidden;text-align:center}
.team-card__photo{height:68px;background:linear-gradient(180deg,#c7ced6,#eef0f2)}
.team-card__name{font:700 6.3px/1.2 "Raleway",sans-serif;margin-top:3px}
.team-card__role{font-size:5.4px;color:#6c7a8c}
.team-card ul{list-style:none;text-align:left;margin:8px 0 0 20px;font-size:5.8px;line-height:1.75}
.col-num{position:absolute;font:500 17px/1 "Raleway",sans-serif}
.col-head{position:absolute;font:700 6.4px/1.6 "Raleway",sans-serif;width:140px}
.col-body{position:absolute;width:140px;font-size:6.4px;line-height:1.7}
</style>
</head>
<body>
<svg width="0" height="0" style="position:absolute">
  <defs>
    <symbol id="i-check" viewBox="0 0 24 24"><circle class="ico" cx="12" cy="12" r="9"/><circle class="ico" cx="12" cy="12" r="5.5"/><path class="ico" d="M9.5 12l1.8 1.8 3.4-3.6"/></symbol>
    <symbol id="i-clock" viewBox="0 0 24 24"><path class="ico" d="M19 11A8 8 0 1 0 12 20"/><path class="ico" d="M11 7v5l3 2"/><circle class="ico" cx="18" cy="18" r="3.5"/><path class="ico" d="M18 16.5v3M16.5 18h3"/></symbol>
    <symbol id="i-grow" viewBox="0 0 24 24"><path class="ico" d="M3 17c3 0 4-2 7-2h4M3 21h11l6-4"/><path class="ico" d="M9 12V9M13 12V6M17 12V4"/><path class="ico" d="M15 4l2-2 2 2"/></symbol>
    <symbol id="i-split" viewBox="0 0 24 24"><path class="ico" d="M12 21V11M12 11L6 6M12 11l6-5M12 3v4"/><path class="ico" d="M9.5 5L12 2.5 14.5 5M4 9V5h4M20 9V5h-4"/></symbol>
    <symbol id="i-play" viewBox="0 0 10 10"><path d="M1 0.5L9.5 5 1 9.5z" fill="#143357"/></symbol>
  </defs>
</svg>

<div class="board">

  <!-- Cover -->
  <section class="slide slide--blue" style="left:77px;top:102px">
    <div class="brand" style="left:38px;top:36px"><span class="brand__dot"></span><span class="brand__name">KLUVOTREN</span></div>
    <h1 class="cover-title" style="left:34px;top:110px">Your Presentation<br>Title <em>Goes Here</em></h1>
    <div class="btn" style="left:34px;top:183px;width:176px"><svg><use href="#i-play"/></svg>Lorem ipsum dolor sit amet</div>
    <p class="cover-foot" style="left:34px">07 Februar 2025 &nbsp;|&nbsp; Created by Lena Beispiel</p>
    <p class="cover-foot" style="right:23px">info@kluvotrens.de &nbsp;|&nbsp; www.kluvotrens.de</p>
    <div class="photo photo--fade" style="left:270px;top:-10px;width:104px;height:90px" role="img" aria-label="Foto: Behandlung in der Praxis"></div>
    <div class="photo" style="left:270px;top:88px;width:104px;height:140px" role="img" aria-label="Foto: Tierärztin mit Hund"></div>
    <div class="photo photo--fade" style="left:270px;top:238px;width:104px;height:60px" role="img" aria-label="Foto: Team bei der Arbeit"></div>
    <div class="photo photo--fade" style="left:383px;top:-10px;width:105px;height:58px" role="img" aria-label="Foto: Praxisalltag"></div>
    <div class="photo" style="left:383px;top:57px;width:105px;height:140px" role="img" aria-label="Foto: Teamhände übereinander"></div>
    <div class="photo" style="left:383px;top:206px;width:105px;height:72px" role="img" aria-label="Foto: junger Hund"></div>
  </section>

  <!-- Agenda 1 -->
  <section class="slide" style="left:598px;top:102px">
    <h2 class="slide-title" style="left:24px">Today’s Agenda</h2>
    <div class="mark"><span class="mark__dot"></span><span class="mark__name">KLUVOTREN</span></div>
    <div class="pattern-area" role="img" aria-label="dezentes dekoratives Punktmuster in der Ecke"></div>
    <div class="agenda-item" style="left:97px;top:112px"><b>01</b><div><strong>Lorem ipsum dolor sit amet</strong>• Lorem ipsum dolor sit amet<br>• Lorem ipsum dolor sit amet</div></div>
    <div class="agenda-item" style="left:262px;top:112px"><b>02</b><div><strong>Lorem ipsum dolor sit amet</strong>• Lorem ipsum dolor sit amet<br>• Lorem ipsum dolor sit amet</div></div>
    <div class="agenda-item" style="left:139px;top:159px"><b>03</b><div><strong>Lorem ipsum dolor sit amet</strong>• Lorem ipsum dolor sit amet<br>• Lorem ipsum dolor sit amet</div></div>
    <div class="agenda-item" style="left:304px;top:159px"><b>04</b><div><strong>Lorem ipsum dolor sit amet</strong>• Lorem ipsum dolor sit amet<br>• Lorem ipsum dolor sit amet</div></div>
    <div class="agenda-item" style="left:166px;top:206px"><b>05</b><div><strong>Lorem ipsum dolor sit amet</strong>• Lorem ipsum dolor sit amet<br>• Lorem ipsum dolor sit amet</div></div>
    <div class="agenda-item" style="left:331px;top:206px"><b>06</b><div><strong>Lorem ipsum dolor sit amet</strong>• Lorem ipsum dolor sit amet<br>• Lorem ipsum dolor sit amet</div></div>
  </section>

  <!-- Agenda 2 -->
  <section class="slide" style="left:77px;top:405px">
    <h2 class="slide-title">Today’s Agenda</h2>
    <div class="mark"><span class="mark__dot"></span><span class="mark__name">KLUVOTREN</span></div>
    <div class="abs" style="left:0;top:135px;width:218px;height:150px;background:var(--blue);border-radius:0 22px 0 0"></div>
    <div class="photo" style="left:40px;top:82px;width:158px;height:166px;border-radius:14px" role="img" aria-label="Foto: Tierärztin am Laptop"></div>
    <div class="list-row" style="top:89px"><b>01</b><span>Lorem ipsum dolor sit amet, consectetuer<br>adipiscing elit, sed diam nonummy.</span></div>
    <div class="rule" style="top:122px"></div>
    <div class="list-row" style="top:133px"><b>02</b><span>Lorem ipsum dolor sit amet, consectetuer<br>adipiscing elit, sed diam nonummy.</span></div>
    <div class="rule" style="top:166px"></div>
    <div class="list-row" style="top:177px"><b>03</b><span>Lorem ipsum dolor sit amet, consectetuer<br>adipiscing elit, sed diam nonummy.</span></div>
    <div class="rule" style="top:210px"></div>
    <div class="list-row" style="top:220px"><b>04</b><span>Lorem ipsum dolor sit amet, consectetuer<br>adipiscing elit, sed diam nonummy.</span></div>
  </section>

  <!-- One Long Column -->
  <section class="slide" style="left:598px;top:405px">
    <h2 class="slide-title" style="font-size:16px;top:34px">One Long Column</h2>
    <div class="mark"><span class="mark__dot"></span><span class="mark__name">KLUVOTREN</span></div>
    <p class="bold abs" style="left:38px;top:89px;width:240px">Lorem ipsum dolor sit amet, consectetuer adipiscing elit, sed diam nonummy nibh euismod tincidunt.</p>
    <p class="txt abs" style="left:38px;top:124px;width:436px">Lorem ipsum dolor sit amet, consectetuer adipiscing elit, sed diam nonummy nibh euismod tincidunt ut laoreet dolore magna aliquam erat volutpat. Ut wisi enim ad minim veniam, quis nostrud exerci tation ullamcorper suscipit lobortis nisl ut aliquip ex ea commodo consequat. Duis autem vel eum iriure dolor in hendrerit in vulputate velit esse molestie consequat, vel illum dolore eu feugiat nulla</p>
    <p class="txt abs" style="left:38px;top:176px;width:436px">Lorem ipsum dolor sit amet, consectetuer adipiscing elit, sed diam nonummy nibh euismod tincidunt ut laoreet dolore magna aliquam erat volutpat. Ut wisi enim ad minim veniam, quis nostrud exerci tation ullamcorper suscipit lobortis nisl ut aliquip ex ea commodo consequat. Duis autem vel eum iriure dolor in hendrerit in vulputate velit esse molestie consequat, vel illum dolore eu feugiat nulla</p>
    <p class="foot">Your presentation Title Goes Here &nbsp;|&nbsp; www.kluvotrens.de</p>
    <div class="pg">02</div>
  </section>

  <!-- Four Panel Point -->
  <section class="slide" style="left:77px;top:709px">
    <h2 class="slide-title">Four Panel Point</h2>
    <div class="mark"><span class="mark__dot"></span><span class="mark__name">KLUVOTREN</span></div>
    <p class="txt abs" style="left:38px;top:73px;width:440px">Lorem ipsum dolor sit amet, consectetuer adipiscing elit, sed diam nonummy nibh euismod tincidunt ut laoreet dolore magna aliquam erat volutpat. Ut wisi enim ad minim veniam.</p>
    <div class="abs" style="left:0;top:215px;width:507px;height:70px;background:var(--blue)"></div>
    <div class="card" style="left:37px;top:122px;width:100px;height:109px"></div>
    <div class="card" style="left:150px;top:122px;width:100px;height:109px"></div>
    <div class="card" style="left:263px;top:122px;width:100px;height:109px"></div>
    <div class="card" style="left:376px;top:122px;width:100px;height:109px"></div>
    <div class="icon-box" style="left:33px;top:116px;width:32px;height:30px"><svg width="20" height="20"><use href="#i-check"/></svg></div>
    <div class="icon-box" style="left:146px;top:116px;width:32px;height:30px"><svg width="20" height="20"><use href="#i-grow"/></svg></div>
    <div class="icon-box" style="left:259px;top:116px;width:32px;height:30px"><svg width="20" height="20"><use href="#i-clock"/></svg></div>
    <div class="icon-box" style="left:372px;top:116px;width:32px;height:30px"><svg width="20" height="20"><use href="#i-split"/></svg></div>
    <p class="bold abs" style="left:73px;top:129px;font-size:6px">Lorem ipsum<br>dolor sit amet.</p>
    <p class="bold abs" style="left:186px;top:129px;font-size:6px">Lorem ipsum<br>dolor sit amet.</p>
    <p class="bold abs" style="left:299px;top:129px;font-size:6px">Lorem ipsum<br>dolor sit amet.</p>
    <p class="bold abs" style="left:412px;top:129px;font-size:6px">Lorem ipsum<br>dolor sit amet.</p>
    <p class="txt abs" style="left:51px;top:153px;width:82px;font-size:5.8px">Lorem ipsum dolor sit amet, consectetuer adipiscing elit, sed diam nonummy nibh euismod tincidunt ut laoreet dolore magna aliquam erat volutpat.</p>
    <p class="txt abs" style="left:164px;top:153px;width:82px;font-size:5.8px">Lorem ipsum dolor sit amet, consectetuer adipiscing elit, sed diam nonummy nibh euismod tincidunt ut laoreet dolore magna aliquam erat volutpat.</p>
    <p class="txt abs" style="left:277px;top:153px;width:82px;font-size:5.8px">Lorem ipsum dolor sit amet, consectetuer adipiscing elit, sed diam nonummy nibh euismod tincidunt ut laoreet dolore magna aliquam erat volutpat.</p>
    <p class="txt abs" style="left:390px;top:153px;width:82px;font-size:5.8px">Lorem ipsum dolor sit amet, consectetuer adipiscing elit, sed diam nonummy nibh euismod tincidunt ut laoreet dolore magna aliquam erat volutpat.</p>
    <p class="foot foot--light">Your presentation Title Goes Here &nbsp;|&nbsp; www.kluvotrens.de</p>
    <div class="pg pg--yellow">03</div>
  </section>

  <!-- Image With Text -->
  <section class="slide" style="left:598px;top:709px">
    <div class="abs" style="left:355px;top:0;width:152px;height:285px;background:var(--blue)"></div>
    <h2 class="slide-title">Image With Text</h2>
    <div class="mark"><span class="mark__dot"></span><span class="mark__name">KLUVOTREN</span></div>
    <div class="photo" style="left:266px;top:70px;width:222px;height:172px;border-radius:12px" role="img" aria-label="Foto: Tierärztin untersucht ein Pferd"></div>
    <p class="bold abs" style="left:38px;top:72px;width:200px">Lorem ipsum dolor sit amet, consectetuer adipiscing elit, sed diam nonummy nibh euismod tincidunt.</p>
    <p class="txt abs" style="left:38px;top:106px;width:212px">Lorem ipsum dolor sit amet, consectetuer adipiscing elit, sed diam nonummy nibh euismod tincidunt ut laoreet dolore magna aliquam erat volutpat. Ut wisi enim ad minim veniam, quis nostrud exerci tation ullamcorper suscipit lobortis nisl ut aliquip ex ea commodo consequat.</p>
    <div class="abs" style="left:38px;top:188px;width:3px;height:30px;background:var(--blue)"></div>
    <p class="txt abs" style="left:52px;top:184px;width:190px;font-style:italic">Lorem ipsum dolor sit amet, consectetuer adipiscing elit, sed diam nonummy nibh euismod tincidunt ut laoreet dolore magna aliquam erat volutpat.</p>
    <p class="foot">Your presentation Title Goes Here &nbsp;|&nbsp; www.kluvotrens.de</p>
    <div class="pg">04</div>
  </section>

  <!-- Single Paragraph -->
  <section class="slide" style="left:77px;top:1012px">
    <h2 class="slide-title">Single Paragraph</h2>
    <div class="mark"><span class="mark__dot"></span><span class="mark__name">KLUVOTREN</span></div>
    <p class="bold abs" style="left:38px;top:92px;width:200px">Lorem ipsum dolor sit amet, consectetuer adipiscing elit, sed diam nonummy nibh euismod tincidunt.</p>
    <p class="txt abs" style="left:38px;top:126px;width:214px">Lorem ipsum dolor sit amet, consectetuer adipiscing elit, sed diam nonummy nibh euismod tincidunt ut laoreet dolore magna aliquam erat volutpat. Ut wisi enim ad minim veniam, quis nostrud exerci tation ullamcorper suscipit lobortis nisl ut aliquip ex ea commodo consequat. Duis autem vel eum iriure dolor in hendrerit in vulputate velit esse molestie consequat, vel illum dolore eu feugiat nulla</p>
    <div class="abs" style="left:287px;top:70px;width:176px;height:162px;background:var(--blue);border-radius:10px">
      <p class="abs" style="left:0;top:8px;width:176px;text-align:center;font:800 26px/1 'Raleway',sans-serif;color:var(--yellow)">“</p>
      <p class="txt abs" style="left:14px;top:40px;width:150px;color:var(--white);font-style:italic">Lorem ipsum dolor sit amet, consectetuer adipiscing elit, sed diam nonummy nibh euismod tincidunt ut laoreet dolore magna aliquam erat volutpat. Ut wisi enim ad minim veniam, quis nostrud exerci tation ullamcorper suscipit lobortis nisl ut aliquip ex ea commodo consequat. dolore eu feugiat nulla</p>
    </div>
    <p class="foot">Your presentation Title Goes Here &nbsp;|&nbsp; www.kluvotrens.de</p>
    <div class="pg">05</div>
  </section>

  <!-- Project Overview -->
  <section class="slide" style="left:598px;top:1012px">
    <h2 class="slide-title">Project Overview</h2>
    <div class="mark"><span class="mark__dot"></span><span class="mark__name">KLUVOTREN</span></div>
    <div class="quart quart--white" style="left:180px;top:75px;border-radius:20px 0 0 0">Quartal<br>One</div>
    <div class="quart quart--blue" style="left:260px;top:73px;border-radius:0 20px 0 0">Quartal<br>Two</div>
    <div class="quart quart--blue" style="left:175px;top:155px;border-radius:0 0 0 20px">Quartal<br>Three</div>
    <div class="quart quart--white" style="left:255px;top:153px;border-radius:0 0 20px 0">Quartal<br>Four</div>
    <svg class="abs" style="left:0;top:0" width="507" height="285">
      <g fill="none" stroke="#143357" stroke-width=".7">
        <path d="M108 91H170L185 104"/><path d="M375 91H345L327 104"/>
        <path d="M108 178H172L185 190"/><path d="M375 178H345L328 190"/>
      </g>
      <g fill="#143357"><circle cx="185" cy="104" r="1.8"/><circle cx="327" cy="104" r="1.8"/><circle cx="185" cy="190" r="1.8"/><circle cx="328" cy="190" r="1.8"/></g>
    </svg>
    <div class="plist" style="left:40px;top:84px"><strong>Quartal 1 Projects</strong>• Project 1 Name goes here<br>• Project 2 Name goes here<br>• Project 3 Name goes here<br>• Project 4 Name goes here</div>
    <div class="plist" style="left:379px;top:84px"><strong>Quartal 2 Projects</strong>• Project 1 Name goes here<br>• Project 2 Name goes here<br>• Project 3 Name goes here<br>• Project 4 Name goes here</div>
    <div class="plist" style="left:40px;top:171px"><strong>Quartal 3 Projects</strong>• Project 1 Name goes here<br>• Project 2 Name goes here<br>• Project 3 Name goes here<br>• Project 4 Name goes here</div>
    <div class="plist" style="left:379px;top:171px"><strong>Quartal 3 Projects</strong>• Project 1 Name goes here<br>• Project 2 Name goes here<br>• Project 3 Name goes here<br>• Project 4 Name goes here</div>
    <p class="foot">Your presentation Title Goes Here &nbsp;|&nbsp; www.kluvotrens.de</p>
    <div class="pg">06</div>
  </section>

  <!-- Our Service (cards) -->
  <section class="slide" style="left:77px;top:1315px">
    <h2 class="slide-title">Our Service</h2>
    <div class="mark"><span class="mark__dot"></span><span class="mark__name">KLUVOTREN</span></div>
    <div class="abs" style="left:0;top:115px;width:507px;height:120px;background:var(--blue)"></div>
    <div class="card" style="left:46px;top:73px;width:200px;height:83px"></div>
    <div class="card" style="left:260px;top:73px;width:200px;height:83px"></div>
    <div class="card" style="left:46px;top:163px;width:200px;height:78px"></div>
    <div class="card" style="left:260px;top:163px;width:200px;height:78px"></div>
    <div class="icon-box" style="left:50px;top:78px;width:60px;height:72px;border-radius:8px"><svg width="30" height="30"><use href="#i-check"/></svg></div>
    <div class="icon-box" style="left:264px;top:78px;width:60px;height:72px;border-radius:8px"><svg width="30" height="30"><use href="#i-clock"/></svg></div>
    <div class="icon-box" style="left:50px;top:168px;width:60px;height:68px;border-radius:8px"><svg width="30" height="30"><use href="#i-grow"/></svg></div>
    <div class="icon-box" style="left:264px;top:168px;width:60px;height:68px;border-radius:8px"><svg width="30" height="30"><use href="#i-split"/></svg></div>
    <p class="txt abs" style="left:120px;top:90px;width:120px"><b class="bold">Lorem ipsum dolor sit amet.</b><br>Lorem ipsum dolor sit amet, consectetuer adipiscing elit, sed diam nonummy nibh euismod.</p>
    <p class="txt abs" style="left:334px;top:90px;width:120px"><b class="bold">Lorem ipsum dolor sit amet.</b><br>Lorem ipsum dolor sit amet, consectetuer adipiscing elit, sed diam nonummy nibh euismod.</p>
    <p class="txt abs" style="left:120px;top:180px;width:120px"><b class="bold">Lorem ipsum dolor sit amet.</b><br>Lorem ipsum dolor sit amet, consectetuer adipiscing elit, sed diam nonummy nibh euismod.</p>
    <p class="txt abs" style="left:334px;top:180px;width:120px"><b class="bold">Lorem ipsum dolor sit amet.</b><br>Lorem ipsum dolor sit amet, consectetuer adipiscing elit, sed diam nonummy nibh euismod.</p>
    <p class="foot">Your presentation Title Goes Here &nbsp;|&nbsp; www.kluvotrens.de</p>
    <div class="pg">11</div>
  </section>

  <!-- Our Team (single) -->
  <section class="slide" style="left:598px;top:1315px">
    <div class="abs" style="left:0;top:0;width:158px;height:285px;background:var(--blue)"></div>
    <h2 class="slide-title" style="left:32px;color:var(--white);line-height:1.25">Our<br>Team</h2>
    <div class="abs" style="left:32px;top:22px;width:22px;height:2px;background:var(--white)"></div>
    <div class="mark"><span class="mark__dot"></span><span class="mark__name">KLUVOTREN</span></div>
    <div class="photo" style="left:98px;top:68px;width:122px;height:170px;border-radius:12px 0 0 0;background:linear-gradient(180deg,#d6dbe1,#5d7390 70%,#143357)" role="img" aria-label="Porträtfoto: Geschäftsführer"></div>
    <p class="abs" style="left:98px;top:203px;width:122px;text-align:center;font:700 8.5px/1.2 'Raleway',sans-serif;color:var(--yellow)">Dr. Jonas Wendler</p>
    <p class="abs" style="left:98px;top:215px;width:122px;text-align:center;font:600 7px/1.2 'Raleway',sans-serif;color:var(--white)">Geschäftsführer</p>
    <p class="bold abs" style="left:245px;top:80px;width:205px;font-style:italic">Lorem ipsum dolor sit amet, consectetuer adipiscing elit, sed diam nonummy nibh euismod tincidunt.</p>
    <p class="txt abs" style="left:245px;top:110px;width:215px">Lorem ipsum dolor sit amet, consectetuer adipiscing elit, sed diam nonummy nibh euismod tincidunt ut laoreet dolore magna aliquam erat volutpat.</p>
    <p class="txt abs" style="left:245px;top:148px;width:230px;display:flex;gap:10px"><span>01</span><span>Lorem ipsum dolor sit amet, consectetuer adipiscing elit, sed diam nonummy nibh euismod.</span></p>
    <p class="txt abs" style="left:245px;top:177px;width:230px;display:flex;gap:10px"><span>02</span><span>Lorem ipsum dolor sit amet, consectetuer adipiscing elit, sed diam nonummy nibh euismod.</span></p>
    <p class="txt abs" style="left:245px;top:206px;width:230px;display:flex;gap:10px"><span>03</span><span>Lorem ipsum dolor sit amet, consectetuer adipiscing elit, sed diam nonummy nibh euismod.</span></p>
    <p class="foot">Your presentation Title Goes Here &nbsp;|&nbsp; www.kluvotrens.de</p>
    <div class="pg">07</div>
  </section>

  <!-- Our Service (image + pills) -->
  <section class="slide" style="left:77px;top:1619px">
    <h2 class="slide-title">Our Service</h2>
    <div class="mark"><span class="mark__dot"></span><span class="mark__name">KLUVOTREN</span></div>
    <div class="abs" style="left:0;top:110px;width:255px;height:175px;background:var(--blue);border-radius:0 22px 0 0"></div>
    <div class="photo" style="left:38px;top:68px;width:196px;height:174px;border-radius:12px;background:linear-gradient(150deg,#f4f5f7,#c9ced5)" role="img" aria-label="Foto: Computertomograph in der Klinik"></div>
    <div class="pill" style="top:74px">Lorem ipsum dolor sit amet,<br>consectetuer adipiscing elit, sed diam.<span class="pill__icon"><svg width="13" height="13"><use href="#i-check"/></svg></span></div>
    <div class="pill" style="top:118px">Lorem ipsum dolor sit amet,<br>consectetuer adipiscing elit, sed diam.<span class="pill__icon"><svg width="13" height="13"><use href="#i-clock"/></svg></span></div>
    <div class="pill" style="top:162px">Lorem ipsum dolor sit amet,<br>consectetuer adipiscing elit, sed diam.<span class="pill__icon"><svg width="13" height="13"><use href="#i-grow"/></svg></span></div>
    <div class="pill" style="top:205px">Lorem ipsum dolor sit amet,<br>consectetuer adipiscing elit, sed diam.<span class="pill__icon"><svg width="13" height="13"><use href="#i-split"/></svg></span></div>
    <p class="foot foot--light">Your presentation Title Goes Here &nbsp;|&nbsp; www.kluvotrens.de</p>
    <div class="pg">12</div>
  </section>

  <!-- Our Team (four) -->
  <section class="slide" style="left:598px;top:1619px">
    <h2 class="slide-title">Our Team</h2>
    <div class="mark"><span class="mark__dot"></span><span class="mark__name">KLUVOTREN</span></div>
    <div class="abs" style="left:0;top:220px;width:507px;height:65px;background:var(--blue)"></div>
    <div class="team-card" style="left:40px"><div class="team-card__photo" role="img" aria-label="Porträtfoto Teammitglied"></div><p class="team-card__name">Dr. Jonas Wendler</p><p class="team-card__role">Geschäftsführer</p><ul><li>• Project 1 Name</li><li>• Project 1 Name</li><li>• Project 1 Name</li><li>• Project 1 Name</li></ul></div>
    <div class="team-card" style="left:155px"><div class="team-card__photo" role="img" aria-label="Porträtfoto Teammitglied"></div><p class="team-card__name">Hedda Lorenzen</p><p class="team-card__role">Geschäftsführer</p><ul><li>• Project 1 Name</li><li>• Project 1 Name</li><li>• Project 1 Name</li><li>• Project 1 Name</li></ul></div>
    <div class="team-card" style="left:270px"><div class="team-card__photo" role="img" aria-label="Porträtfoto Teammitglied"></div><p class="team-card__name">Tobias Kranz</p><p class="team-card__role">Geschäftsführer</p><ul><li>• Project 1 Name</li><li>• Project 1 Name</li><li>• Project 1 Name</li><li>• Project 1 Name</li></ul></div>
    <div class="team-card" style="left:385px"><div class="team-card__photo" role="img" aria-label="Porträtfoto Teammitglied"></div><p class="team-card__name">Clara Vossberg</p><p class="team-card__role">Geschäftsführerin</p><ul><li>• Project 1 Name</li><li>• Project 1 Name</li><li>• Project 1 Name</li><li>• Project 1 Name</li></ul></div>
    <p class="foot foot--light">Your presentation Title Goes Here &nbsp;|&nbsp; www.kluvotrens.de</p>
    <div class="pg pg--yellow">08</div>
  </section>

  <!-- Three Column (intro) -->
  <section class="slide" style="left:77px;top:1922px">
    <h2 class="slide-title">Three Column</h2>
    <div class="mark"><span class="mark__dot"></span><span class="mark__name">KLUVOTREN</span></div>
    <p class="txt abs" style="left:38px;top:66px;width:395px">Lorem ipsum dolor sit amet, consectetuer adipiscing elit, sed diam nonummy nibh euismod tincidunt ut laoreet dolore magna aliquam erat volutpat. Ut wisi enim ad minim veniam, quis nostrud exerci tation ullamcorper suscipit lobortis nisl ut aliquip ex ea commodo consequat.</p>
    <p class="col-num" style="left:38px;top:116px">01</p><p class="col-num" style="left:193px;top:116px">02</p><p class="col-num" style="left:348px;top:116px">03</p>
    <p class="col-head" style="left:38px;top:138px">Lorem ipsum dolor sit amet, consectetuer adipiscing elit, sed diam.</p>
    <p class="col-head" style="left:193px;top:138px">Lorem ipsum dolor sit amet, consectetuer adipiscing elit, sed diam.</p>
    <p class="col-head" style="left:348px;top:138px">Lorem ipsum dolor sit amet, consectetuer adipiscing elit, sed diam.</p>
    <p class="col-body" style="left:38px;top:164px">Lorem ipsum dolor sit amet, consectetuer adipiscing elit, sed diam nonummy nibh euismod tincidunt ut laoreet dolore magna aliquam erat volutpat. Ut wisi enim ad minim veniam, quis nostrud exerci tation ullamcorper suscipit lobortis nisl ut aliquip ex ea.</p>
    <p class="col-body" style="left:193px;top:164px">Lorem ipsum dolor sit amet, consectetuer adipiscing elit, sed diam nonummy nibh euismod tincidunt ut laoreet dolore magna aliquam erat volutpat. Ut wisi enim ad minim veniam, quis nostrud exerci tation ullamcorper suscipit lobortis nisl ut aliquip ex ea.</p>
    <p class="col-body" style="left:348px;top:164px">Lorem ipsum dolor sit amet, consectetuer adipiscing elit, sed diam nonummy nibh euismod tincidunt ut laoreet dolore magna aliquam erat volutpat. Ut wisi enim ad minim veniam, quis nostrud exerci tation ullamcorper suscipit lobortis nisl ut aliquip ex ea.</p>
    <p class="foot">Your presentation Title Goes Here &nbsp;|&nbsp; www.kluvotrens.de</p>
    <div class="pg">09</div>
  </section>

  <!-- Three Column (divided) -->
  <section class="slide" style="left:598px;top:1922px">
    <h2 class="slide-title">Three Column</h2>
    <div class="mark"><span class="mark__dot"></span><span class="mark__name">KLUVOTREN</span></div>
    <div class="abs" style="left:165px;top:95px;width:.7px;height:145px;background:var(--blue)"></div>
    <div class="abs" style="left:320px;top:95px;width:.7px;height:145px;background:var(--blue)"></div>
    <p class="col-num" style="left:38px;top:96px">01</p><p class="col-num" style="left:192px;top:96px">02</p><p class="col-num" style="left:346px;top:96px">03</p>
    <p class="col-head" style="left:38px;top:116px;width:115px">Lorem ipsum dolor sit amet, consectetuer adipiscing.</p>
    <p class="col-head" style="left:192px;top:116px;width:115px">Lorem ipsum dolor sit amet, consectetuer adipiscing.</p>
    <p class="col-head" style="left:346px;top:116px;width:115px">Lorem ipsum dolor sit amet, consectetuer adipiscing.</p>
    <p class="col-body" style="left:38px;top:142px;width:115px">Lorem ipsum dolor sit amet, consectetuer adipiscing elit, sed diam nonummy nibh euismod tincidunt ut laoreet dolore magna aliquam erat volutpat. Ut wisi enim ad minim veniam, quis nostrud exerci tation ullamcorper suscipit lobortis nisl ut aliquip ex ea.</p>
    <p class="col-body" style="left:192px;top:142px;width:115px">Lorem ipsum dolor sit amet, consectetuer adipiscing elit, sed diam nonummy nibh euismod tincidunt ut laoreet dolore magna aliquam erat volutpat. Ut wisi enim ad minim veniam, quis nostrud exerci tation ullamcorper suscipit lobortis nisl ut aliquip ex ea.</p>
    <p class="col-body" style="left:346px;top:142px;width:115px">Lorem ipsum dolor sit amet, consectetuer adipiscing elit, sed diam nonummy nibh euismod tincidunt ut laoreet dolore magna aliquam erat volutpat. Ut wisi enim ad minim veniam, quis nostrud exerci tation ullamcorper suscipit lobortis nisl ut aliquip ex ea.</p>
    <p class="foot">Your presentation Title Goes Here &nbsp;|&nbsp; www.kluvotrens.de</p>
    <div class="pg">10</div>
  </section>

  <!-- Closing -->
  <section class="slide slide--blue" style="left:77px;top:2226px">
    <div class="photo photo--fade" style="left:10px;top:-10px;width:105px;height:67px" role="img" aria-label="Foto: Praxisalltag"></div>
    <div class="photo" style="left:10px;top:88px;width:105px;height:138px" role="img" aria-label="Foto: Tierärztin mit Pferd"></div>
    <div class="photo photo--fade" style="left:10px;top:236px;width:105px;height:60px" role="img" aria-label="Foto: Behandlung"></div>
    <div class="photo photo--fade" style="left:124px;top:-10px;width:104px;height:57px" role="img" aria-label="Foto: Praxisalltag"></div>
    <div class="photo" style="left:124px;top:57px;width:104px;height:121px" role="img" aria-label="Foto: Team am Laptop"></div>
    <div class="photo" style="left:124px;top:188px;width:104px;height:105px" role="img" aria-label="Foto: junger Hund"></div>
    <div class="brand" style="left:290px;top:38px"><span class="brand__dot"></span><span class="brand__name">KLUVOTREN</span></div>
    <h2 class="cover-title" style="left:287px;top:108px">Thank You for<br><em>Your Attention</em></h2>
    <div class="btn" style="left:287px;top:182px;width:176px"><svg><use href="#i-play"/></svg>Lorem ipsum dolor sit amet</div>
    <p class="cover-foot" style="left:19px">info@kluvotrens.de &nbsp;|&nbsp; www.kluvotrens.de</p>
    <p class="cover-foot" style="right:44px">07 Februar 2025 &nbsp;|&nbsp; Created by Lena Beispiel</p>
  </section>

</div>
</body>
</html>
```